Global Consulting firm needs a Business Card Design (Contest)

We need a business card design for a company with global reach called 'Harborline Group'. Harborline Group is a Trusted Procurement Advisor that consults for Zenith 400 and Meridian 900 companies to find cost reductions in their spending. We would like to see designs that communicate fiduciary trust and sense of partnership. The Front should have our logo w/ 'trusted procurement advisor', Employee name and title, company address, email, phone and fax (logo attached "Harbor line group final"). The color scheme and basic concept should be consistent with our presentation front page (attached "HLG presentation cover page"). The Back should have our website (www.hlinellc.com) and an array of our areas of expertise: office supplies, lab supplies, wireless telecom, MRO and IT (see "lab supplies" file for example).

```html
<!DOCTYPE html>
<html lang="en">
<head>
<meta charset="utf-8">
<title>Harborline Group – Business Card</title>
<link rel="stylesheet" href="https://fonts.googleapis.com/css2?family=Gelasio:ital,wght@0,400;0,500;1,400&family=PT+Sans:wght@400;700&display=swap">
<style>
  :root {
    --backdrop: #e9e6e1;
    --card: #ffffff;
    --gold: #c9962a;
    --ink: #1a1a1a;
    --map-tone: #f3ebdc;
    --band: #151515;
    --navy: #1f3a8a;
    --tile-border: #2a3f8f;
    --tier-orange: #e4572e;
    --tier-blue: #2fa8d8;
    --tier-red: #d92430;
    --tier-yellow: #e8d21e;
    --tier-grey: #4a4a4a;
  }
  * { margin: 0; padding: 0; box-sizing: border-box; }
  html, body { width: 1200px; height: 1000px; overflow: hidden; }
  body { background: var(--backdrop); position: relative; font-family: "PT Sans", sans-serif; color: var(--ink); }

  .card {
    position: absolute; left: 265px; width: 665px; height: 396px;
    background: var(--card); border-radius: 22px; overflow: hidden;
    box-shadow: 0 2px 8px rgba(0,0,0,0.12);
  }
  .card--front { top: 73px; }
  .card--back { top: 533px; }

  /* Front */
  .world-map {
    position: absolute; left: 40px; top: 8px; width: 600px; height: 320px;
    background: radial-gradient(ellipse at 50% 45%, var(--map-tone) 0%, rgba(243,235,220,0.6) 55%, rgba(255,255,255,0) 75%);
  }
  .person { position: absolute; left: 0; width: 665px; top: 84px; text-align: center; }
  .person__name { font-weight: 700; font-size: 28px; color: var(--gold); line-height: 30px; }
  .person__title { font-size: 24px; line-height: 26px; color: var(--ink); letter-spacing: 0.5px; }

  .tier-graphic {
    position: absolute; left: 33px; top: 137px; width: 156px; height: 122px;
    background: linear-gradient(180deg, var(--tier-orange) 0%, var(--tier-blue) 30%, var(--tier-red) 50%, var(--tier-yellow) 70%, var(--tier-grey) 100%);
    opacity: 0.85;
  }

  .wordmark-front {
    position: absolute; right: 32px; top: 214px;
    font-family: "Gelasio", serif; font-size: 37px; color: var(--ink); white-space: nowrap;
  }
  .divider { position: absolute; left: 33px; right: 32px; top: 276px; height: 2px; background: var(--gold); }

  .contacts { position: absolute; left: 33px; top: 288px; list-style: none; }
  .contacts li { display: flex; align-items: center; height: 27px; font-size: 19px; }
  .contacts svg { width: 21px; height: 21px; margin-right: 7px; flex: none; }

  .office { position: absolute; right: 32px; top: 290px; text-align: right; }
  .office__company { font-weight: 700; font-size: 18px; color: var(--gold); line-height: 24px; letter-spacing: 0.3px; }
  .office__city { font-size: 19px; line-height: 26px; }

  /* Back */
  .brand { position: absolute; left: 0; width: 665px; top: 94px; display: flex; justify-content: center; align-items: center; }
  .brand__mark { width: 42px; height: 42px; border-radius: 50%; background: var(--gold); margin-right: 16px; }
  .brand__name { font-family: "Gelasio", serif; font-size: 36px; color: var(--ink); white-space: nowrap; }
  .tagline {
    position: absolute; left: 0; width: 665px; top: 140px; text-align: center;
    font-family: "Gelasio", serif; font-style: italic; font-size: 19px; color: var(--ink);
  }
  .web-band {
    position: absolute; left: 0; right: 0; top: 185px; height: 24px; background: var(--band);
    text-align: center; color: var(--gold); font-weight: 700; font-size: 16px; line-height: 24px; letter-spacing: 3px;
  }
  .expertise { position: absolute; left: 45px; top: 235px; width: 580px; height: 80px; list-style: none; }
  .expertise__item { position: absolute; top: 0; width: 106px; height: 80px; }
  .expertise__tab {
    position: absolute; left: 6px; top: 0; height: 14px; padding: 0 10px 0 8px;
    background: var(--navy); color: #fff; font-size: 10px; line-height: 14px; border-radius: 3px 8px 0 0; white-space: nowrap;
  }
  .expertise__photo { position: absolute; left: 0; top: 8px; width: 106px; height: 71px; border: 1px solid var(--tile-border); }
  .photo--office { background: linear-gradient(135deg, #f5a3c7, #f7e27a 50%, #8fd0f0); }
  .photo--lab { background: linear-gradient(135deg, #f2f4f7, #c9d4e6 60%, #e8a0c8); }
  .photo--telecom { background: linear-gradient(135deg, #1e4fa8, #5a8fd6 55%, #c7d9ef); }
  .photo--mro { background: linear-gradient(135deg, #ffffff, #cfd3d8 55%, #8e949b); }
  .photo--shipping { background: linear-gradient(135deg, #c9a27a, #b27f54 55%, #5a5a5a); }
</style>
</head>
<body>

<section class="card card--front" aria-label="Card front">
  <div class="world-map" role="img" aria-label="Faint world map in the background"></div>

  <div class="person">
    <p class="person__name">Daniel Ashworth</p>
    <p class="person__title">Manager</p>
  </div>

  <div class="tier-graphic" role="img" aria-label="Illustration of a colourful layered pyramid of service levels"></div>

  <p class="wordmark-front">Harborline Group</p>
  <div class="divider"></div>

  <ul class="contacts">
    <li>
      <svg viewBox="0 0 21 21" aria-hidden="true"><circle cx="10.5" cy="10.5" r="9.5" fill="none" stroke="#c9962a" stroke-width="1.6"/><path d="M6 9 Q10.5 5 15 9 L13.5 10.5 L12 9.5 L9 9.5 L7.5 10.5 Z M8 11 H13 L14 15 H7 Z" fill="#c9962a"/></svg>
      855 - 410 - 3872
    </li>
    <li>
      <svg viewBox="0 0 21 21" aria-hidden="true"><circle cx="10.5" cy="10.5" r="9.5" fill="none" stroke="#c9962a" stroke-width="1.6"/><rect x="7.5" y="5.5" width="6" height="4" fill="#c9962a"/><rect x="5.5" y="9" width="10" height="5" rx="1" fill="#c9962a"/><rect x="7.5" y="13" width="6" height="3" fill="#fff" stroke="#c9962a" stroke-width="0.8"/></svg>
      609 - 555 - 0148
    </li>
    <li>
      <svg viewBox="0 0 21 21" aria-hidden="true"><circle cx="10.5" cy="10.5" r="9.5" fill="none" stroke="#c9962a" stroke-width="1.6"/><rect x="5.5" y="7" width="10" height="7" fill="none" stroke="#c9962a" stroke-width="1.3"/><path d="M5.5 7 L10.5 11 L15.5 7" fill="none" stroke="#c9962a" stroke-width="1.3"/></svg>
      info@hlinellc.com
    </li>
  </ul>

  <div class="office">
    <p class="office__company">HARBORLINE GROUP</p>
    <p class="office__city">Cedar Crest, New Jersey</p>
  </div>
</section>

<section class="card card--back" aria-label="Card back">
  <div class="brand">
    <span class="brand__mark" aria-hidden="true"></span>
    <span class="brand__name">Harborline Group</span>
  </div>
  <p class="tagline">Trusted Procurement Advisor</p>
  <div class="web-band">www.hlinellc.com</div>

  <ul class="expertise">
    <li class="expertise__item" style="left:0">
      <div class="expertise__photo photo--office" role="img" aria-label="Photo of office supplies"></div>
      <span class="expertise__tab">Office Supplies</span>
    </li>
    <li class="expertise__item" style="left:118px">
      <div class="expertise__photo photo--lab" role="img" aria-label="Photo of lab glassware"></div>
      <span class="expertise__tab">Lab Supplies</span>
    </li>
    <li class="expertise__item" style="left:238px">
      <div class="expertise__photo photo--telecom" role="img" aria-label="Photo of a mobile phone over a globe"></div>
      <span class="expertise__tab">Wireless Telecom</span>
    </li>
    <li class="expertise__item" style="left:358px">
      <div class="expertise__photo photo--mro" role="img" aria-label="Photo of a wrench and bolt"></div>
      <span class="expertise__tab">MRO</span>
    </li>
    <li class="expertise__item" style="left:470px">
      <div class="expertise__photo photo--shipping" role="img" aria-label="Photo of a scanner over a parcel"></div>
      <span class="expertise__tab">Shipping/Postage</span>
    </li>
  </ul>
</section>

</body>
</html>
```